Italian restaurant needs new site

Need to make our website better.

Must have reservation module

Must be able to sell wine tasting tours and wine pairing tours and intégrate with dunmo desk

Blog

Social media

Wandervane ranking and last review.
Updates

Number of Pages Required

1 page

Font styles to use
Serif

Requirements
Must have
• Reservation module
• Marketplace to buy wine pairings and gift certificates
• Wandervane review
• Kindlepost posts
• All info from old site

```html
<!DOCTYPE html>
<html lang="en">
<head>
<meta charset="utf-8">
<title>Vellora Bistro</title>
<link href="https://fonts.googleapis.com/css2?family=Lora:ital,wght@0,400;0,700;1,400&family=Roboto:wght@400;500&display=swap" rel="stylesheet">
<style>
:root{
  --wine:#8e1b22;
  --wine-dark:#6e1016;
  --ink:#2b2b2b;
  --muted:#666;
  --light:#f4f4f4;
  --footer:#3a3a3a;
  --white:#fff;
  --star:#d9a520;
}
*{box-sizing:border-box;margin:0;padding:0}
html,body{width:1200px;height:2795px;overflow:hidden;background:var(--white)}
body{font-family:'Roboto',sans-serif;color:var(--ink);position:relative}
.abs{position:absolute}
/* header */
.site-header{position:absolute;top:0;left:0;width:1200px;height:105px;background:var(--white);border-top:4px solid var(--wine-dark);z-index:2}
.brand{position:absolute;left:88px;top:-10px;width:172px;height:198px;border-radius:0 0 86px 86px;background:var(--white);z-index:3;text-align:center;padding-top:58px}
.brand-name{font-family:'Lora',serif;color:var(--wine);font-size:27px;letter-spacing:1px;line-height:1.15}
.brand-tag{font-family:'Lora',serif;font-size:8.5px;color:var(--wine);letter-spacing:.5px;margin-top:8px;border-top:1px solid var(--wine);display:inline-block;padding-top:4px}
.nav{position:absolute;top:47px;left:0;font-size:12px;font-weight:500}
.nav a{position:absolute;white-space:nowrap;color:var(--ink);text-decoration:none}
.nav a.active{color:var(--wine)}
.search{position:absolute;left:1068px;top:30px;width:45px;height:45px;border:1.5px solid var(--wine);border-radius:50%}
/* hero */
.hero{position:absolute;top:105px;left:0;width:1200px;height:540px;background:radial-gradient(ellipse at 60% 40%,#5a4034 0%,#2a1a15 55%,#140c0a 100%)}
.hero h1{position:absolute;top:180px;width:100%;text-align:center;font-family:'Lora',serif;font-style:italic;font-weight:400;font-size:60px;color:var(--white)}
.hero p{position:absolute;top:265px;left:290px;width:620px;text-align:center;color:var(--white);font-size:12.5px;line-height:26px}
.btn{position:absolute;background:var(--wine);color:var(--white);font-size:13px;font-weight:500;text-align:center;border-radius:3px}
/* tours */
.tours{position:absolute;top:645px;left:0;width:1200px;height:500px;background:var(--light)}
.script{font-family:'Lora',serif;font-style:italic;color:var(--wine);font-size:28px}
.tours .script{position:absolute;top:145px;left:120px;width:440px;text-align:center}
.tours h2{position:absolute;top:190px;left:100px;width:480px;text-align:center;font-size:24px;font-weight:500}
.tours p{position:absolute;top:238px;left:130px;width:420px;text-align:center;font-size:12px;line-height:26px;color:var(--muted)}
.photo{position:absolute}
/* reservation */
.reserve{position:absolute;top:1145px;left:0;width:1200px;height:460px}
.reserve-photo{position:absolute;left:0;top:0;width:583px;height:460px;background:radial-gradient(ellipse at 55% 70%,#8a5a2c 0%,#4a3222 45%,#2a2420 100%)}
.arrow{position:absolute;top:214px;width:34px;height:34px;border-radius:50%;background:rgba(255,255,255,.85)}
.reserve-form{position:absolute;left:583px;top:0;width:617px;height:460px;background:linear-gradient(180deg,var(--wine) 0%,#7a141a 100%)}
.reserve-form .script{position:absolute;top:38px;width:100%;text-align:center;color:#2a0a0c}
.reserve-form h2{position:absolute;top:78px;width:100%;text-align:center;color:var(--white);font-size:26px;font-weight:500}
.rule{position:absolute;top:95px;height:1px;width:46px;background:rgba(255,255,255,.7)}
.field{position:absolute;background:var(--white);height:40px;width:230px;font-size:10px;color:#555;padding:13px 12px;border-radius:2px}
.submit{position:absolute;left:47px;top:392px;width:112px;height:40px;background:#141414;color:var(--white);font-size:12px;font-weight:500;text-align:center;line-height:40px}
/* blog */
.blog{position:absolute;top:1605px;left:0;width:1200px;height:555px}
.blog h2{position:absolute;top:30px;width:100%;text-align:center;font-size:26px;font-weight:500}
.blog .lead{position:absolute;top:75px;width:100%;text-align:center;font-size:11.5px;color:#444}
.post{position:absolute;top:123px;width:325px}
.post-img{height:207px}
.post h3{font-size:14px;font-weight:500;margin-top:30px;padding-bottom:12px;border-bottom:1px solid #e3e3e3}
.meta{font-size:9px;color:#999;padding:12px 0;border-bottom:1px solid #e3e3e3;display:flex;justify-content:space-between}
.post p{font-size:11.5px;line-height:21px;color:#444;margin-top:12px}
/* rating */
.rating{position:absolute;top:2160px;left:0;width:1200px;height:320px;background:#f2f3f5}
.badge{position:absolute;left:147px;top:57px;width:210px;height:210px;border-radius:50%;background:var(--white);border:4px solid #e6e6e6;display:flex;align-items:center;justify-content:center;gap:8px;font-size:28px;color:#222}
.badge i{display:block;width:14px;height:14px;border-radius:50%;background:#2f8a4a}
.rating h3{position:absolute;left:414px;top:65px;font-size:15px;font-weight:500}
.rating p{position:absolute;left:418px;top:103px;width:700px;font-size:11px;line-height:23px;color:#777}
/* footer */
.site-footer{position:absolute;top:2480px;left:0;width:1200px;height:315px;background:var(--footer);color:var(--white)}
.foot-brand{position:absolute;left:120px;top:100px;width:230px;text-align:center}
.foot-brand .brand-name{color:var(--white);font-size:34px}
.foot-brand .brand-tag{color:var(--white);border-color:var(--white);font-size:11px}
.foot-col{position:absolute;top:50px}
.foot-col h4{font-size:15px;font-weight:500;margin-bottom:24px}
.foot-col li{list-style:none;font-size:11px;line-height:16px;margin-bottom:13px;padding-left:30px;position:relative}
.foot-col li svg{position:absolute;left:0;top:1px}
.foot-col p{font-size:11px;line-height:20px}
.subscribe-input{width:210px;height:34px;background:var(--white);color:#777;font-size:11px;padding:11px 12px;margin-top:14px}
.subscribe-btn{display:inline-block;margin-top:10px;background:var(--wine);font-size:9.5px;padding:7px 10px}
.copyright{position:absolute;left:86px;top:275px;font-size:11px}
.social{position:absolute;top:264px;width:36px;height:36px;border:1.5px solid var(--white);border-radius:50%}
</style>
</head>
<body>

<header class="site-header">
  <nav class="nav">
    <a class="active" style="left:383px">HOME</a>
    <a style="left:470px">MENU</a>
    <a style="left:558px">RESERVATIONS</a>
    <a style="left:697px">BLOG</a>
    <a style="left:782px">REVIEW</a>
    <a style="left:878px">GALLERY</a>
    <a style="left:983px">CONTACT US</a>
  </nav>
  <div class="search">
    <svg width="45" height="45" viewBox="0 0 45 45"><circle cx="21" cy="21" r="4" fill="none" stroke="#8e1b22" stroke-width="1.8"/><line x1="24" y1="24" x2="27" y2="27" stroke="#8e1b22" stroke-width="1.8"/></svg>
  </div>
</header>
<div class="brand">
  <div class="brand-name">VELLORA<br>BISTRO</div>
  <div class="brand-tag">ITALIAN CUISINE &amp; WINE BAR</div>
</div>

<section class="hero" role="img" aria-label="Candlelit restaurant table with wine glasses, plated dish and a red rose">
  <h1>Vellora Bistro</h1>
  <p>Vellora Bistro Located in the heart of downtown, across from Corra Lane Plaza, just two short blocks up from Halvern Resort and the Alba marina is Vellora Bistro, a place with great original Southern</p>
  <div class="btn" style="left:522px;top:340px;width:155px;height:46px;line-height:46px">READ MORE</div>
</section>

<section class="tours">
  <div class="script">Sell Wine Tasting</div>
  <h2>TOURS &amp; WINE PAIRING TOURS</h2>
  <p>Vellora Bistro Located in the heart of downtown, across from Corra Lane Plaza, just two short blocks up from Halvern Resort and the Alba marina is Vellora Bistro, a place with great original Southern Italian and Mediterranean cuisine and a European touch. Sure to enjoy your classic favorites tails.</p>
  <div class="btn" style="left:264px;top:368px;width:158px;height:48px;line-height:48px">READ MORE INFO</div>
  <div class="photo" role="img" aria-label="Oak wine barrels in a cellar" style="left:619px;top:53px;width:158px;height:395px;background:linear-gradient(180deg,#3a2418,#8a5a34 50%,#4a2e1c)"></div>
  <div class="photo" role="img" aria-label="White wine bottle and glasses with grapes in a vineyard" style="left:787px;top:53px;width:157px;height:395px;background:linear-gradient(180deg,#9cb75a,#dfe6c8 50%,#6f8a3a)"></div>
  <div class="photo" role="img" aria-label="Red wine being poured into a glass" style="left:954px;top:53px;width:158px;height:395px;background:linear-gradient(180deg,#5a2c2a,#b08a78 50%,#4a1c1e)"></div>
</section>

<section class="reserve">
  <div class="reserve-photo" role="img" aria-label="Burger with fries being served at the table"></div>
  <div class="arrow" style="left:16px"><svg width="34" height="34" viewBox="0 0 34 34"><path d="M19 11l-6 6 6 6" fill="none" stroke="#333" stroke-width="2"/></svg></div>
  <div class="arrow" style="left:533px"><svg width="34" height="34" viewBox="0 0 34 34"><path d="M15 11l6 6-6 6" fill="none" stroke="#333" stroke-width="2"/></svg></div>
  <div class="reserve-form">
    <div class="script">Specials Offers</div>
    <h2>MAKE RESERVATIONS</h2>
    <div class="rule" style="left:97px"></div>
    <div class="rule" style="left:474px"></div>
    <div class="field" style="left:47px;top:145px">NAME ON RESERVATION :</div>
    <div class="field" style="left:288px;top:145px">EMAIL :</div>
    <div class="field" style="left:47px;top:196px">PHONE :</div>
    <div class="field" style="left:288px;top:196px">PERSONS :</div>
    <div class="field" style="left:47px;top:247px">DATE:</div>
    <div class="field" style="left:288px;top:247px">TIME :</div>
    <div class="field" style="left:47px;top:298px;width:471px;height:78px">MESSAGE :</div>
    <div class="submit">SUBMIT</div>
  </div>
</section>

<section class="blog">
  <h2>LATEST BLOG</h2>
  <div class="lead">We offer, a variety of homemade fresh cooked dishes derived from generations-old family recipes, accompanied</div>
  <article class="post" style="left:86px">
    <div class="post-img" role="img" aria-label="Warm-lit restaurant dining room" style="background:linear-gradient(160deg,#5a3a24,#a27048 50%,#3a2618)"></div>
    <h3>INVITE YOU TO COME &amp; ENJOY</h3>
    <div class="meta"><span>27 MARCH 2017</span><span>120</span><span>LIKE</span><span>SHARE</span></div>
    <p>Alba local residents Marco Venti from the Kestrel stores, Tomas Ribal from the local legend band Blue Lantern and Owen Harte of Alba</p>
  </article>
  <article class="post" style="left:437px">
    <div class="post-img" role="img" aria-label="Chef spooning sauce onto a plated dish" style="background:linear-gradient(160deg,#cfcfcf,#6a6a6a 50%,#2a2a2a)"></div>
    <h3>OUR EXQUISITE RANGE OF UNIQUE</h3>
    <div class="meta"><span>27 MARCH 2017</span><span>120</span><span>LIKE</span><span>SHARE</span></div>
    <p>Alba local residents Marco Venti from the Kestrel stores, Tomas Ribal from the local legend band Blue Lantern and Owen Harte of Alba</p>
  </article>
  <article class="post" style="left:788px">
    <div class="post-img" role="img" aria-label="Set tables with wine glasses" style="background:linear-gradient(160deg,#3a2a24,#9a7a68 50%,#2a1e1a)"></div>
    <h3>MEDITERRANEAN CUISINE</h3>
    <div class="meta"><span>27 MARCH 2017</span><span>120</span><span>LIKE</span><span>SHARE</span></div>
    <p>Alba local residents Marco Venti from the Kestrel stores, Tomas Ribal from the local legend band Blue Lantern and Owen Harte of Alba</p>
  </article>
</section>

<section class="rating">
  <svg class="abs" style="left:50px;top:110px" width="20" height="100" viewBox="0 0 20 100"><path d="M18 0L2 50l16 50" fill="none" stroke="#ccc" stroke-width="1.5"/></svg>
  <svg class="abs" style="left:1132px;top:110px" width="20" height="100" viewBox="0 0 20 100"><path d="M2 0l16 50L2 100" fill="none" stroke="#ccc" stroke-width="1.5"/></svg>
  <div class="badge"><i></i>Wandervane</div>
  <h3>WANDERVANE TRAVELER RATING</h3>
  <p>Vellora Bistro Located in the heart of downtown, across from Corra Lane Plaza, just two short blocks up from Halvern Resort and the Alba marina is Vellora Bistro, a place with great original Southern Italian and Mediterranean cuisine and a European touch. Sure to enjoy your classic favorites or satisfy even the most distinctive pallet We offer, a variety of hom-emational and international wines and fun Italian inspired cocktails.</p>
  <svg class="abs" style="left:418px;top:224px" width="80" height="14" viewBox="0 0 80 14">
    <g fill="none" stroke="#d9a520" stroke-width="1">
      <path id="s" d="M7 1l1.8 3.8 4.1.5-3 2.8.8 4.1L7 10.2 3.3 12.2l.8-4.1-3-2.8 4.1-.5z"/>
      <use href="#s" x="15"/><use href="#s" x="30"/><use href="#s" x="45"/>
    </g>
    <path d="M67 1l1.8 3.8 4.1.5-3 2.8.8 4.1L67 10.2 63.3 12.2l.8-4.1-3-2.8 4.1-.5z" fill="#d9a520"/>
  </svg>
</section>

<footer class="site-footer">
  <div class="foot-brand">
    <div class="brand-name">VELLORA<br>BISTRO</div>
    <div class="brand-tag">ITALIAN CUISINE &amp; WINE BAR</div>
  </div>
  <div class="foot-col" style="left:410px">
    <h4>CONTACT US</h4>
    <ul>
      <li><svg width="13" height="13" viewBox="0 0 13 13"><path d="M2 1h3l1 3-2 1a7 7 0 0 0 4 4l1-2 3 1v3a1 1 0 0 1-1 1A11 11 0 0 1 1 2a1 1 0 0 1 1-1z" fill="#fff"/></svg>555 0148 (Phone)</li>
      <li><svg width="13" height="13" viewBox="0 0 13 13"><rect x="1" y="4" width="11" height="6" fill="#fff"/><rect x="3" y="1" width="7" height="3" fill="#fff"/></svg>555 0149 (Fax)</li>
      <li><svg width="13" height="13" viewBox="0 0 13 13"><rect x="1" y="3" width="11" height="8" fill="#fff"/><path d="M1 3l5.5 4L12 3" stroke="#3a3a3a" fill="none"/></svg><u>info@vellorabistro.com</u></li>
      <li><svg width="13" height="14" viewBox="0 0 13 14"><path d="M6.5 1a4 4 0 0 1 4 4c0 3-4 8-4 8s-4-5-4-8a4 4 0 0 1 4-4z" fill="#fff"/><circle cx="6.5" cy="5" r="1.5" fill="#3a3a3a"/></svg>Calle Norte 14, Centro<br>Puerto Alba</li>
    </ul>
  </div>
  <div class="foot-col" style="left:653px;width:220px">
    <h4>NEWSLETTER SIGNUP</h4>
    <p>Register Your email address to get information about us</p>
    <div class="subscribe-input">Email Address</div>
    <span class="subscribe-btn">SUBSCRIBE</span>
  </div>
  <div class="foot-col" style="left:907px;width:210px">
    <h4>CHIRPLINE FEED</h4>
    <ul><li><svg width="13" height="13" viewBox="0 0 13 13"><circle cx="6.5" cy="6.5" r="5" fill="#fff"/></svg>Vellora Bistro, a place with great original Southern Italian &amp; Med terranean cuisine and a Euro your classic favorites<br><br><span style="color:#bbb">1 month ago</span></li></ul>
  </div>
  <div class="copyright">© Copyright 2017 Vellora Bistro.All Rights Reserved</div>
  <div class="social" style="left:903px" aria-label="Kindlepost"></div>
  <div class="social" style="left:946px" aria-label="Chirpline"></div>
  <div class="social" style="left:989px"></div>
  <div class="social" style="left:1032px"></div>
  <div class="social" style="left:1075px"></div>
</footer>

</body>
</html>
```